Business Card Design Project

Business Card
We are rebranding with a new logo
Industry/Entity Type
Business
Contact Information for Business Card
Dennis Morvale +61 487215963 dennis@quorv.com.au P.O. Box 872 Fernlow QLD 4309
Requirements
Must have
- Logo

```html
<!DOCTYPE html>
<html lang="en">
<head>
<meta charset="utf-8">
<title>Quorv International – Business Card</title>
<link rel="stylesheet" href="https://fonts.googleapis.com/css2?family=Open+Sans:wght@400;600;700&display=swap">
<style>
  :root {
    --page-bg: #2a2a2a;
    --card-white: #f4f4f4;
    --blue-deep: #0b5d7c;
    --blue-mid: #12789e;
    --blue-shadow: #0a4a63;
    --blue-icon: #1386b8;
    --text-grey: #4a4a4a;
    --name-white: #ffffff;
  }
  * { margin: 0; padding: 0; box-sizing: border-box; }
  html, body {
    width: 1200px;
    height: 915px;
    overflow: hidden;
    background: var(--page-bg);
    font-family: "Open Sans", sans-serif;
  }
  .card {
    position: absolute;
    left: 120px;
    top: 180px;
    width: 960px;
    height: 555px;
    background: var(--card-white);
    overflow: hidden;
  }
  .card-swoosh {
    position: absolute;
    inset: 0;
    width: 960px;
    height: 555px;
  }
  .holder-name {
    position: absolute;
    left: 54px;
    top: 36px;
    font-size: 26px;
    font-weight: 700;
    color: var(--name-white);
    letter-spacing: 0.3px;
  }
  .brand-name {
    position: absolute;
    right: 58px;
    top: 250px;
    font-size: 44px;
    font-weight: 600;
    color: var(--blue-mid);
    letter-spacing: 1px;
  }
  .contact-list {
    position: absolute;
    right: 62px;
    top: 380px;
    list-style: none;
    text-align: right;
  }
  .contact-item {
    display: flex;
    justify-content: flex-end;
    align-items: center;
    gap: 12px;
    font-size: 22px;
    line-height: 31px;
    color: var(--text-grey);
  }
  .contact-icon { width: 18px; height: 18px; flex: none; }
  .postal-address {
    position: absolute;
    right: 60px;
    top: 484px;
    font-size: 23px;
    color: var(--text-grey);
  }
</style>
</head>
<body>
  <section class="card">
    <svg class="card-swoosh" viewBox="0 0 960 555" aria-hidden="true">
      <defs>
        <radialGradient id="swoosh-fill" cx="0.35" cy="0.15" r="0.8">
          <stop offset="0" stop-color="#1a8ab3"/>
          <stop offset="1" stop-color="#0a5574"/>
        </radialGradient>
      </defs>
      <path d="M0 0 H640 C380 40 70 210 0 555 Z" fill="url(#swoosh-fill)"/>
      <path d="M640 0 C380 40 70 210 0 555 L0 530 C80 200 380 30 640 0 Z" fill="var(--blue-shadow)"/>
      <path d="M640 0 C400 50 110 220 0 555 L0 555 C70 210 380 40 640 0 Z" fill="var(--blue-shadow)" opacity="0.35"/>
    </svg>

    <h1 class="holder-name">DENNIS MORVALE</h1>

    <p class="brand-name">Quorv International</p>

    <ul class="contact-list">
      <li class="contact-item">+61 487215963
        <svg class="contact-icon" viewBox="0 0 18 18"><path d="M3 6 Q9 1 15 6 L13 8 L11 6 H7 L5 8 Z" fill="var(--blue-icon)"/><rect x="4" y="9" width="10" height="6" rx="1.5" fill="var(--blue-icon)"/></svg>
      </li>
      <li class="contact-item">dennis@quorv.com.au
        <svg class="contact-icon" viewBox="0 0 18 18"><rect x="2" y="4" width="14" height="10" rx="1.5" fill="var(--blue-icon)"/><path d="M2.5 5 L9 10 L15.5 5" stroke="#fff" stroke-width="1.3" fill="none"/></svg>
      </li>
      <li class="contact-item">www.quorv.com.au
        <svg class="contact-icon" viewBox="0 0 18 18"><circle cx="9" cy="9" r="7" fill="var(--blue-icon)"/><path d="M6 5 Q9 7 7 10 Q10 11 9 14 M11 4 Q12 7 14 7" stroke="#fff" stroke-width="1.3" fill="none"/></svg>
      </li>
    </ul>

    <p class="postal-address">P.O. Box 872, Fernlow QLD 4309</p>
  </section>
</body>
</html>
```